Business Card Design

We need a business card designed for our new company. Prefer a black card with white logo & writing.

Contact Information for Business Card

Ted Galloway, address: 7-4812 Fernhollow Road, Abbotsford, BC, V3K 8R2, Office Phone: 604-712-3390, Cell: 604-947-2164, Email: ted@resinworkshub.ca

Colors

Designer to choose only greyscale colors for use in the design.

```html
<!DOCTYPE html>
<html lang="en">
<head>
<meta charset="utf-8">
<title>Resinworks Hub – Business Card</title>
<link href="https://fonts.googleapis.com/css2?family=Poppins:wght@300;400;800&display=swap" rel="stylesheet">
<style>
  :root {
    --stage: #222223;
    --card: #1c1c1e;
    --ink: #ffffff;
    --muted: #d9d9d9;
    --art-light: #3c3c3f;
    --art-dark: #1c1c1e;
  }
  * { margin: 0; padding: 0; box-sizing: border-box; }
  html, body { width: 1200px; height: 711px; overflow: hidden; }
  body {
    background: var(--stage);
    font-family: "Poppins", sans-serif;
    color: var(--ink);
    position: relative;
  }
  .card {
    position: absolute;
    top: 201px;
    width: 540px;
    height: 309px;
    background: var(--card);
    border-radius: 18px;
    overflow: hidden;
    box-shadow: 0 0 0 1px #3a3a3c, 0 12px 30px rgba(0,0,0,.45);
  }
  .card--front { left: 40px; }
  .card--back { left: 620px; }

  .brand {
    display: flex;
    align-items: center;
    gap: 12px;
    font-weight: 800;
    text-transform: uppercase;
    line-height: 1;
    color: var(--ink);
    white-space: nowrap;
  }
  .brand__square {
    width: 22px; height: 22px;
    background: var(--ink);
  }
  .card--front .brand {
    position: absolute;
    left: 50%; top: 50%;
    transform: translate(-50%, -50%);
    font-size: 40px;
    letter-spacing: 1px;
  }
  .card--back .brand {
    position: absolute;
    left: 30px; top: 34px;
    font-size: 24px;
  }
  .card--back .brand__square { width: 14px; height: 14px; }

  .ridge-art {
    position: absolute;
    right: 0; bottom: 0;
    width: 230px; height: 170px;
    background: linear-gradient(160deg, var(--art-light) 0%, var(--art-dark) 85%);
  }
  .owner {
    position: absolute;
    right: 28px; top: 78px;
    text-align: right;
  }
  .owner__name {
    font-size: 28px;
    line-height: 1;
    white-space: nowrap;
  }
  .owner__first { font-weight: 800; }
  .owner__last { font-weight: 300; }
  .owner__role {
    font-size: 13px;
    font-weight: 400;
    color: var(--muted);
    margin-top: 4px;
  }

  .address {
    position: absolute;
    left: 30px; top: 150px;
    font-weight: 300;
    font-size: 13px;
    line-height: 1.35;
  }
  .contact-list {
    position: absolute;
    left: 30px; top: 200px;
    list-style: none;
    font-weight: 300;
    font-size: 13px;
    line-height: 1;
  }
  .contact-list li {
    display: flex;
    align-items: center;
    gap: 10px;
    margin-bottom: 8px;
  }
  .contact-list svg { width: 13px; height: 13px; flex: none; }
</style>
</head>
<body>
  <section class="card card--front">
    <div class="brand"><span class="brand__square"></span>Resinworks Hub</div>
  </section>

  <section class="card card--back">
    <div class="brand"><span class="brand__square"></span>Resinworks Hub</div>

    <div class="ridge-art" role="img" aria-label="Glossy greyscale mountain ridge illustration"></div>

    <div class="owner">
      <div class="owner__name"><span class="owner__first">Ted</span> <span class="owner__last">Galloway</span></div>
      <div class="owner__role">Owner</div>
    </div>

    <p class="address">7-4812 Fernhollow Road,<br>Abbotsford, BC, V3K 8R2.</p>

    <ul class="contact-list">
      <li>
        <svg viewBox="0 0 16 16" fill="none" stroke="#fff" stroke-width="1.6"><path d="M3 2h3l1.5 4-2 1.2a9 9 0 0 0 3.3 3.3L10 8.5l4 1.5v3a1 1 0 0 1-1 1A12 12 0 0 1 2 3a1 1 0 0 1 1-1z"/></svg>
        604-712-3390
      </li>
      <li>
        <svg viewBox="0 0 16 16" fill="none" stroke="#fff" stroke-width="1.6"><rect x="4" y="1" width="8" height="14" rx="1.5"/><circle cx="8" cy="12.3" r=".7" fill="#fff"/></svg>
        604-947-2164
      </li>
      <li>
        <svg viewBox="0 0 16 16" fill="none" stroke="#fff" stroke-width="1.4"><circle cx="8" cy="8" r="6.5"/><ellipse cx="8" cy="8" rx="2.8" ry="6.5"/><path d="M1.5 8h13"/></svg>
        www.resinworkshub.ca
      </li>
      <li>
        <svg viewBox="0 0 16 16" fill="none" stroke="#fff" stroke-width="1.5"><rect x="1.5" y="3.5" width="13" height="9" rx="1"/><path d="M1.5 4l6.5 5 6.5-5"/></svg>
        ted@resinworkshub.ca
      </li>
    </ul>
  </section>
</body>
</html>
```